At Home Pet Euthanasia - business cards & brand stationary

We already have a logo and the colors and a website. Need a business card designed that will be able to customized to multiple veterinarians who will be partnering with us. The feel needs to be compassionate, comforting with our tagline 'A Gift of Love at Home'. It will be 2 sides.
On the back our platform/partner vets will be customizing each business card with their own service areas, phone numbers, name and title. On the front, i would like to see experimentation with use of our photos, the logo, tagline and a description 'Peaceful and Compassionate At-Home Pet Euthanasia'

```html
<!DOCTYPE html>
<html lang="en">
<head>
<meta charset="utf-8">
<title>Willowden – Business Card</title>
<link href="https://fonts.googleapis.com/css2?family=Poppins:wght@300;400;500;600&display=swap" rel="stylesheet">
<style>
  :root{
    --brand-blue:#7b9cc6;
    --brand-blue-deep:#6a8dbb;
    --ink:#1f1f22;
    --paper:#ffffff;
    --backdrop:#e9e7e4;
    --photo-grey-dark:#4a4a4a;
    --photo-grey-light:#bdbdbd;
    --photo-green:#4f8a3a;
    --photo-cream:#efe9df;
  }
  *{box-sizing:border-box;margin:0;padding:0}
  html,body{width:1200px;height:900px;overflow:hidden}
  body{background:var(--backdrop);font-family:"Poppins",sans-serif;color:var(--ink);position:relative}

  .card{position:absolute;left:250px;width:700px;height:400px;background:var(--paper);
        box-shadow:0 6px 18px rgba(0,0,0,.18);overflow:hidden}
  .card--front{top:40px}
  .card--back{top:460px}

  .photo-strip{position:absolute;inset:0;width:100%;height:100%}

  .contact-name{position:absolute;left:48px;top:46px;font-size:27px;font-weight:600;color:var(--brand-blue);line-height:1;z-index:2}
  .contact-title{position:absolute;left:48px;top:78px;font-size:19px;font-weight:400;line-height:1;z-index:2}

  .contact-list{position:absolute;left:48px;top:138px;list-style:none;z-index:2}
  .contact-list li{display:flex;align-items:center;gap:10px;font-size:19px;line-height:28px}
  .contact-list svg{width:18px;height:18px;flex:none}

  .contact-address{position:absolute;left:72px;top:236px;font-size:19px;line-height:26px;z-index:2}

  .brand{position:absolute;right:60px;top:62px;text-align:right;z-index:2}
  .brand-mark{display:flex;align-items:center;justify-content:flex-end;gap:12px}
  .brand-square{width:30px;height:30px;background:var(--brand-blue)}
  .brand-name{font-size:46px;font-weight:600;color:var(--brand-blue);line-height:1}
  .brand-tagline{margin-top:8px;font-size:15px;font-weight:300;color:var(--brand-blue)}

  .wave{position:absolute;left:0;bottom:0;width:700px;height:190px;z-index:1}
  .service-line{position:absolute;right:34px;bottom:28px;font-size:19px;font-weight:500;color:var(--paper);letter-spacing:.3px;line-height:1.3;z-index:3}
</style>
</head>
<body>

  <section class="card card--front" aria-label="Card front">
    <svg class="photo-strip" viewBox="0 0 700 400" preserveAspectRatio="none">
      <defs>
        <linearGradient id="greyPanelA" x1="0" y1="0" x2="1" y2="1">
          <stop offset="0" stop-color="var(--photo-grey-dark)"/>
          <stop offset="1" stop-color="var(--photo-grey-light)"/>
        </linearGradient>
        <linearGradient id="colourPanel" x1="0" y1="0" x2="0" y2="1">
          <stop offset="0" stop-color="var(--photo-cream)"/>
          <stop offset=".55" stop-color="#e6e2da"/>
          <stop offset="1" stop-color="var(--photo-green)"/>
        </linearGradient>
        <linearGradient id="greyPanelB" x1="0" y1="0" x2="1" y2="1">
          <stop offset="0" stop-color="#9a9a9a"/>
          <stop offset="1" stop-color="#e2e2e2"/>
        </linearGradient>
      </defs>
      <polygon role="img" aria-label="Black and white photo of an older dog resting beside its owner" points="0,0 200,0 330,400 0,400" fill="url(#greyPanelA)"/>
      <polygon role="img" aria-label="Colour photo of a small white dog held in its owner's hands on grass" points="206,0 440,0 530,400 336,400" fill="url(#colourPanel)"/>
      <polygon role="img" aria-label="Black and white photo of a tabby cat cuddled against a person's cheek" points="446,0 700,0 700,400 536,400" fill="url(#greyPanelB)"/>
      <line x1="203" y1="0" x2="333" y2="400" stroke="#fff" stroke-width="6"/>
      <line x1="443" y1="0" x2="533" y2="400" stroke="#fff" stroke-width="6"/>
    </svg>
  </section>

  <section class="card card--back" aria-label="Card back">
    <p class="contact-name">Daniel Hart</p>
    <p class="contact-title">Managing Director</p>

    <ul class="contact-list">
      <li>
        <svg viewBox="0 0 24 24" aria-hidden="true"><path fill="var(--brand-blue)" d="M6.6 10.8a15 15 0 0 0 6.6 6.6l2.2-2.2a1 1 0 0 1 1-.25 11.4 11.4 0 0 0 3.6.57 1 1 0 0 1 1 1V20a1 1 0 0 1-1 1A17 17 0 0 1 3 4a1 1 0 0 1 1-1h3.5a1 1 0 0 1 1 1c0 1.25.2 2.45.57 3.6a1 1 0 0 1-.25 1z"/></svg>
        044-987 654 321
      </li>
      <li>
        <svg viewBox="0 0 24 24" aria-hidden="true"><rect x="2" y="5" width="20" height="14" fill="var(--brand-blue)"/><path d="M2 5l10 8 10-8" fill="none" stroke="#fff" stroke-width="1.6"/></svg>
        hello@willowden.example
      </li>
      <li>
        <svg viewBox="0 0 24 24" aria-hidden="true"><circle cx="12" cy="12" r="10" fill="none" stroke="var(--brand-blue)" stroke-width="2"/><ellipse cx="12" cy="12" rx="4.5" ry="10" fill="none" stroke="var(--brand-blue)" stroke-width="1.6"/><path d="M2 12h20M4 7h16M4 17h16" stroke="var(--brand-blue)" stroke-width="1.4"/></svg>
        www.willowden.example
      </li>
    </ul>

    <p class="contact-address">421, Address line goes here<br>45452,Country Name</p>

    <div class="brand">
      <div class="brand-mark">
        <span class="brand-square" aria-hidden="true"></span>
        <span class="brand-name">Willowden</span>
      </div>
      <p class="brand-tagline">A gift of love at home.</p>
    </div>

    <svg class="wave" viewBox="0 0 700 190" preserveAspectRatio="none" aria-hidden="true">
      <path d="M0 100 C 220 112, 430 70, 700 0 L700 190 L0 190 Z" fill="var(--brand-blue)"/>
      <path d="M0 114 C 230 116, 400 84, 560 30" fill="none" stroke="#fff" stroke-width="2"/>
    </svg>
    <p class="service-line">Peaceful and Compassionate At-Home Pet Euthanasia</p>
  </section>

</body>
</html>
```